Looking for a cool & simple business-card-design for digital agency

Hi!

We are a web agency that offers Reputation Management, Vextor & Seo Services and software development. We like cool things, we like innovative styles.

We have uploaded our logo.

Project Deadline Extended Reason: Client does not want any designs with the colorful logo. Please send us submissions ONLY with the blac and white logo. What the client would like to see:1) Back of the card: is a silver logo on a black background2) front of the card with all the data, please use white background and black logo thank you Added Friday, May 8, 2015

Industry/Entity Type

Software

```html
<!DOCTYPE html>
<html lang="en">
<head>
<meta charset="utf-8">
<title>NetPrime AG – Business Card</title>
<link rel="stylesheet" href="https://fonts.googleapis.com/css2?family=Lato:wght@400;700&display=swap">
<style>
  :root {
    --page-bg: #d8d5d1;
    --card-bg: #f3f3f2;
    --card-edge: #c9c9c9;
    --ink: #1f1f1f;
    --ink-soft: #3a3a3a;
    --swoosh: #111111;
  }
  * { margin: 0; padding: 0; box-sizing: border-box; }
  html, body {
    width: 1200px;
    height: 969px;
    overflow: hidden;
    background: var(--page-bg);
    font-family: "Lato", sans-serif;
    color: var(--ink);
  }
  .card {
    position: absolute;
    left: 80px;
    top: 196px;
    width: 1040px;
    height: 577px;
    background: var(--card-bg);
    border: 1px solid var(--card-edge);
    overflow: hidden;
  }
  .card__swoosh {
    position: absolute;
    inset: 0;
    width: 100%;
    height: 100%;
  }
  .card__swoosh path { fill: var(--swoosh); }

  .brand {
    position: absolute;
    top: 84px;
    right: 46px;
    text-align: right;
  }
  .brand__name {
    display: flex;
    align-items: center;
    justify-content: flex-end;
    gap: 18px;
    font-size: 50px;
    font-weight: 700;
    line-height: 1;
    color: var(--ink);
  }
  .brand__mark {
    width: 40px;
    height: 40px;
    background: var(--ink);
  }
  .brand__tagline {
    margin-top: 12px;
    font-size: 22px;
    font-weight: 400;
    letter-spacing: 9px;
    margin-right: -9px;
    color: var(--ink);
  }

  .person {
    position: absolute;
    left: 52px;
    top: 278px;
  }
  .person__name {
    font-size: 31px;
    font-weight: 700;
    color: var(--ink-soft);
  }
  .person__role {
    margin-top: 6px;
    font-size: 24px;
    font-weight: 400;
    color: var(--ink-soft);
  }

  .contact {
    position: absolute;
    left: 52px;
    top: 382px;
    list-style: none;
    font-size: 26px;
    line-height: 37px;
    color: var(--ink-soft);
  }
  .contact__item {
    display: flex;
    align-items: center;
    gap: 9px;
  }
  .contact__icon {
    width: 22px;
    height: 22px;
    flex: none;
  }
  .contact__icon * { fill: none; stroke: var(--ink-soft); stroke-width: 2; }
  .contact__icon .solid { fill: var(--ink-soft); stroke: none; }
  .contact__icon .flap { stroke: var(--card-bg); }

  .services {
    position: absolute;
    left: 466px;
    width: 360px;
    top: 419px;
    list-style: none;
    text-align: center;
    font-size: 26px;
    line-height: 37px;
    color: var(--ink);
  }
</style>
</head>
<body>
  <main class="card">
    <svg class="card__swoosh" viewBox="0 0 793 440" preserveAspectRatio="none" aria-hidden="true">
      <path d="M0 126 C 300 118, 560 190, 793 438 C 560 260, 320 200, 0 188 Z"/>
    </svg>

    <header class="brand">
      <div class="brand__name"><span class="brand__mark"></span>NetPrime AG</div>
      <div class="brand__tagline">DIGITALE STRATEGIEN</div>
    </header>

    <section class="person">
      <h1 class="person__name">Lena Brandt</h1>
      <p class="person__role">Director</p>
    </section>

    <ul class="contact">
      <li class="contact__item">
        <svg class="contact__icon" viewBox="0 0 22 22" aria-hidden="true">
          <path class="solid" d="M2 8 C2 4 20 4 20 8 L20 10 L15 10 L15 8 L7 8 L7 10 L2 10 Z"/>
          <path class="solid" d="M5 11 L17 11 L19 19 L3 19 Z"/>
        </svg>
        041 555 0182
      </li>
      <li class="contact__item">
        <svg class="contact__icon" viewBox="0 0 22 22" aria-hidden="true">
          <rect x="6" y="2" width="10" height="18" rx="2"/>
          <circle class="solid" cx="11" cy="17" r="1"/>
        </svg>
        079 555 0147
      </li>
      <li class="contact__item">
        <svg class="contact__icon" viewBox="0 0 22 22" aria-hidden="true">
          <rect class="solid" x="2" y="5" width="18" height="13"/>
          <path class="flap" d="M2 5 L11 12 L20 5"/>
        </svg>
        info@netprimeag.com
      </li>
      <li class="contact__item">
        <svg class="contact__icon" viewBox="0 0 22 22" aria-hidden="true">
          <circle cx="11" cy="11" r="9"/>
          <ellipse cx="11" cy="11" rx="4" ry="9"/>
          <path d="M2 11 H20 M4 6 H18 M4 16 H18"/>
        </svg>
        www.netprimeag.com
      </li>
    </ul>

    <ul class="services">
      <li>Reputation Management</li>
      <li>Vextor &amp; Seo Services</li>
      <li>Software development.</li>
    </ul>
  </main>
</body>
</html>
```